CBD/HEMP website for e-commerce store

I need a CBD website for my shopify store. I am looking for a layout similar to these site ( https://quietmeadowcbd.com/ ) (https://elmridgecbd.com/) but with my logo and products. I am attaching what my logo looks like so that it helps with the design.

Target Market(s)

CBD HEMP CANNABIS

Industry/Entity Type

Cannabis

Coding

Coded - Design and coding required

Number of Pages Required

5+ page

Requirements
Nice to have
• I would like for it to have a trendy/galaxy feel

```html
<!DOCTYPE html>
<html lang="en">
<head>
<meta charset="utf-8">
<title>Cosmoleaf – Beyond The High</title>
<link href="https://fonts.googleapis.com/css2?family=Roboto:wght@400;500;700&display=swap" rel="stylesheet">
<style>
:root{
  --purple:#8a2fa8;
  --purple-dark:#5e1b78;
  --purple-bright:#a23fc4;
  --green:#6fa972;
  --green-dark:#1e6b2c;
  --panel:#050308;
  --white:#ffffff;
  --muted:#d9d0e0;
  --space-deep:#0b0718;
  --brand-green:#5aa83c;
}
*{box-sizing:border-box;margin:0;padding:0}
html,body{width:1200px;height:2736px;overflow:hidden}
body{
  position:relative;
  font-family:"Roboto",Arial,sans-serif;
  color:var(--white);
  background:
    radial-gradient(ellipse 500px 400px at 900px 2500px,rgba(120,50,170,.55),transparent 70%),
    radial-gradient(ellipse 600px 500px at 150px 2350px,rgba(90,40,150,.5),transparent 70%),
    radial-gradient(ellipse 500px 300px at 600px 120px,rgba(110,40,160,.45),transparent 70%),
    radial-gradient(ellipse 400px 600px at 1150px 1200px,rgba(80,30,130,.45),transparent 70%),
    radial-gradient(ellipse 400px 600px at 40px 1200px,rgba(80,30,130,.45),transparent 70%),
    var(--space-deep);
}
a{color:inherit;text-decoration:none}
.abs{position:absolute}

.promo-bar{left:0;top:0;width:1200px;height:40px;background:var(--purple-dark);
  display:flex;align-items:center;justify-content:center;font-size:15px;letter-spacing:.5px}

.brand-name{left:160px;top:100px;font-size:44px;font-weight:700;color:#c56ee6}
.contact{left:496px;top:98px;font-size:14px;line-height:30px;color:var(--muted)}
.search-btn{left:866px;top:142px;width:36px;height:36px;border-radius:50%;border:2px solid var(--purple-bright);
  display:flex;align-items:center;justify-content:center}
.account{left:924px;top:140px;display:flex;gap:10px}
.account a{height:40px;padding:0 22px;border-radius:8px;background:var(--purple);display:flex;align-items:center;font-size:16px;font-weight:500}

.main-nav{left:80px;top:256px;width:1040px;height:40px;border-radius:14px;background:var(--purple);
  display:flex;justify-content:center;align-items:center;gap:46px;font-size:14px;font-weight:500}

.page-panel{left:80px;top:320px;width:1040px;height:2012px;background:var(--panel)}

.sidebar{left:108px;top:380px;width:244px}
.cat{height:32px;margin-bottom:10px;border-radius:6px;background:var(--purple);display:flex;align-items:center;
  justify-content:space-between;padding:0 12px;font-size:14px}
.box{border-radius:8px;padding:12px 14px;margin-top:4px}
.box h3{font-size:19px;font-weight:700;margin-bottom:10px}
.box.green{background:var(--green)}
.box.purple{background:var(--purple-bright)}
.socials{display:flex;gap:8px;justify-content:center}
.socials span{width:30px;height:30px;border-radius:50%;background:var(--white)}
.news-text{font-size:13px;line-height:18px;margin-bottom:12px}
.news-input{height:32px;background:#fff;border-radius:4px;color:#888;font-size:12px;padding:9px 10px;margin-bottom:14px}
.subscribe{display:inline-block;background:var(--green-dark);padding:10px 22px;border-radius:18px;font-size:14px;font-weight:500}
.pop-item{display:flex;align-items:center;gap:18px;margin-bottom:18px;font-size:14px;line-height:20px}
.pop-thumb{width:56px;height:56px;border-radius:6px;background:radial-gradient(circle,#b7a98a,#5c6b3e)}

.content{left:392px;top:380px;width:700px}
.title-bar{height:68px;background:var(--purple);display:flex;align-items:center;justify-content:center;font-size:34px;font-weight:700}
.hero{position:relative;margin-top:24px;height:384px;background:radial-gradient(ellipse at 50% 45%,#6f9a3f,#2e4a1c 60%,#121a0a)}
.hero .label{position:absolute;left:0;right:0;bottom:26px;text-align:center;font-size:24px;font-weight:500}
.hero .arrow{position:absolute;top:170px;width:36px;height:36px;border-radius:50%;background:var(--purple);display:flex;align-items:center;justify-content:center}
h2.section{font-size:34px;font-weight:700;margin:40px 0 18px}
.grid4{display:flex;gap:18px}
.card4{width:162px;height:216px;background:var(--purple-bright);padding:8px;border-radius:4px;position:relative}
.card4 .img{height:150px;background:radial-gradient(circle,#d5c9a1,#7e8a55 55%,#f4f0ea 56%)}
.card4 .name{font-size:14px;text-align:center;margin-top:8px}
.card4 .price{font-size:13px;text-align:center;margin-top:2px}
.badge-new{position:absolute;left:-6px;top:-6px;width:40px;height:40px;border-radius:50%;background:#3aa0e6}
.grid3{display:flex;gap:32px}
.card3{width:212px;height:216px;background:var(--purple);padding:8px;border-radius:4px}
.card3 .img{height:170px}
.card3 .name{text-align:center;font-size:15px;margin-top:10px}
.about{text-align:center}
.about h2{font-size:38px;font-weight:700;margin:84px 0 20px}
.about p{font-size:14px;line-height:24px;width:540px;margin:0 auto}
.video-title{text-align:center;font-size:38px;font-weight:700;margin:56px 0 34px}
.video{position:relative;height:304px;background:radial-gradient(ellipse at 50% 40%,#d8dde0 0 18%,#3f6e2c 40%,#1a3112)}
.video .play{position:absolute;left:326px;top:128px;width:52px;height:36px;border-radius:8px;background:rgba(20,20,20,.8);display:flex;align-items:center;justify-content:center}
.video .tools{position:absolute;right:10px;top:10px;display:flex;flex-direction:column;gap:10px}
.video .tools span{width:26px;height:26px;border-radius:50%;background:rgba(20,20,20,.75)}
.brands-title{font-size:38px;font-weight:700;margin:60px 0 30px}
.brands{display:flex;justify-content:space-between;align-items:center;height:60px;padding:0 30px}
.brands span{font-size:20px;font-weight:700;color:var(--brand-green);display:flex;align-items:center;gap:8px}
.brands i{width:22px;height:22px;border-radius:50%;background:var(--brand-green);display:inline-block}

.currency{left:550px;top:2386px;width:100px;height:28px;background:#fff;color:#222;border-radius:4px;font-size:13px;
  display:flex;align-items:center;justify-content:center;gap:6px}
.payments{left:414px;top:2458px;display:flex;gap:22px}
.payments span{width:62px;height:30px;background:#fff;border-radius:3px}
.foot-links{left:460px;top:2536px;display:flex;gap:38px;font-size:15px}
.copyright{left:0;top:2664px;width:1200px;text-align:center;font-size:14px}
.chat{left:1138px;top:2666px;font-size:14px}
</style>
</head>
<body>
<div class="abs promo-bar">FREE SHIPPING ON ALL ORDERS OVER $99</div>

<div class="abs brand-name">Cosmoleaf</div>
<div class="abs contact">Call: 1-800-555-0142<br>12 4 Lorem ipsum dolor sit amet,<br>Sed ut perspiciatis</div>
<div class="abs search-btn">
  <svg width="16" height="16" viewBox="0 0 16 16"><circle cx="7" cy="7" r="5" fill="none" stroke="#fff" stroke-width="2"/><line x1="11" y1="11" x2="15" y2="15" stroke="#fff" stroke-width="2"/></svg>
</div>
<div class="abs account"><a href="#">Log In</a><a href="#">Sign up</a></div>

<nav class="abs main-nav">
  <a href="#">HOME</a><a href="#">SHOP</a><a href="#">REVIEWS</a><a href="#">BLOG</a><a href="#">OUR STORY</a><a href="#">WHOLESALE</a><a href="#">CONTACT US</a>
</nav>

<div class="abs page-panel"></div>

<aside class="abs sidebar">
  <div class="cat">Flowers <span>▾</span></div>
  <div class="cat">Pre Rolls <span>▾</span></div>
  <div class="cat">Vapes <span>▾</span></div>
  <div class="cat">CBD Chocolate <span>▾</span></div>
  <div class="cat">Oil Hemp <span>▾</span></div>
  <div class="box green" style="height:100px">
    <h3>Stay in touch</h3>
    <div class="socials"><span></span><span></span><span></span><span></span><span></span></div>
  </div>
  <div class="box purple" style="margin-top:16px;height:232px">
    <h3>Newsletter</h3>
    <p class="news-text">Sign up to our newsletter for the latest news and special offers.</p>
    <div class="news-input">Email...</div>
    <a class="subscribe" href="#">Subscribe</a>
  </div>
  <div class="box green" style="margin-top:24px;height:512px">
    <h3>Popular products</h3>
    <div class="pop-item"><div class="pop-thumb" role="img" aria-label="Quiet Pine flower bud"></div><div>Quiet Pine<br>$12</div></div>
    <div class="pop-item"><div class="pop-thumb" role="img" aria-label="Mango Dusk flower bud"></div><div>Mango Dusk<br>$40</div></div>
    <div class="pop-item"><div class="pop-thumb" role="img" aria-label="Kiro flower bud"></div><div>Kiro<br>$40</div></div>
    <div class="pop-item"><div class="pop-thumb" role="img" aria-label="Oat Cloud flower bud"></div><div>Oat Cloud<br>$40</div></div>
  </div>
</aside>

<main class="abs content">
  <div class="title-bar">Beyond The High</div>
  <div class="hero" role="img" aria-label="Close-up of hemp leaves">
    <span class="arrow" style="left:6px">‹</span>
    <span class="arrow" style="right:6px">›</span>
    <div class="label">Shop CBD</div>
  </div>

  <h2 class="section">Featured collection</h2>
  <div class="grid4">
    <div class="card4"><div class="img" role="img" aria-label="Quiet Pine flower bud"></div><div class="name">Quiet Pine</div><div class="price">$12</div></div>
    <div class="card4"><span class="badge-new"></span><div class="img" role="img" aria-label="Mango Dusk flower bud"></div><div class="name">Mango Dusk</div><div class="price">$40</div></div>
    <div class="card4"><div class="img" role="img" aria-label="Kiro flower bud"></div><div class="name">Kiro</div><div class="price">$40</div></div>
    <div class="card4"><div class="img" role="img" aria-label="Oat Cloud flower bud"></div><div class="name">Oat Cloud</div><div class="price">$40</div></div>
  </div>

  <h2 class="section">Featured collection</h2>
  <div class="grid3">
    <div class="card3"><div class="img" role="img" aria-label="Glowing purple flower" style="background:radial-gradient(circle,#b58ad6,#3b2456 60%,#120a1c)"></div><div class="name">Flowers</div></div>
    <div class="card3"><div class="img" role="img" aria-label="Person on a hill at sunset" style="background:linear-gradient(#2d4f7c,#c9855a 60%,#3a2a20)"></div><div class="name">Pre Rolls</div></div>
    <div class="card3"><div class="img" role="img" aria-label="Portrait with soft light" style="background:linear-gradient(#6c8fb0,#c9a58c)"></div><div class="name">Flowers</div></div>
  </div>

  <section class="about">
    <h2>Beyond the High</h2>
    <p>We believe in providing cannabis that enhances your lifestyle without the side effects commonly associated with THC. In essence, our flowers stay true to the plant, without the overwhelming psycho-activity.</p>
  </section>

  <h2 class="video-title">Our Video</h2>
  <div class="video" role="img" aria-label="Video of a grower in a hemp greenhouse">
    <div class="tools"><span></span><span></span><span></span></div>
    <div class="play"><svg width="16" height="16" viewBox="0 0 16 16"><path d="M3 2l11 6-11 6z" fill="#fff"/></svg></div>
  </div>

  <h2 class="brands-title">Our brands</h2>
  <div class="brands">
    <span>Field Grove</span>
    <span><i></i>Pine Hollow CBD</span>
    <span>Brook Farm</span>
    <span>Sunward Labs</span>
  </div>
</main>

<div class="abs currency">USD $ <span>▾</span></div>
<div class="abs payments"><span></span><span></span><span></span><span></span><span></span></div>
<div class="abs foot-links"><a href="#">Search</a><a href="#">About Us</a><a href="#">FAQ</a><a href="#">Contact</a></div>
<div class="abs copyright">©Copyright2020 Cosmoleaf.com | All right reserved |</div>
<div class="abs chat">Chat</div>
</body>
</html>
```